Postcard design to acquire new clients for my Property Management Company

I'm looking for a postcard design that I can send to prospective clients detailing information about my company and services.
Postcard should be eye catching and contain information from www.bramblecrestpm.com. I've provided a few screen shots for the most important information and my logo.
Target Market(s)
Real Estate
Industry/Entity Type
Real Estate
Font styles to use
Sans Serif
Requirements
Must have
- Must be eye catching!! this will be a direct mail piece - I'd like for the card to be read and not tossed in the trash immediately.
Design que from the logo.
A place to write / print the receipts name and address.
our physical address - 2387 Hollow Pine Road, Lubbock, TX 79852.
Should not have
- the contact information on the business card is not accurate - please use info from website.

```html
<!DOCTYPE html>
<html lang="en">
<head>
<meta charset="utf-8">
<title>Bramblecrest Property Management – Direct Mail Postcard</title>
<link href="https://fonts.googleapis.com/css2?family=Montserrat:wght@300;400;500;600;700;800&display=swap" rel="stylesheet">
<style>
  :root{
    --navy:#1a4887;
    --navy-deep:#163c73;
    --band:#3d5c97;
    --grey:#9a9a9a;
    --grey-light:#b5b5b5;
    --paper:#f3f3f3;
    --white:#ffffff;
    --ink:#5a5a5a;
    --bg:#1d4a86;
  }
  *{box-sizing:border-box;margin:0;padding:0}
  html,body{width:995px;height:1200px;overflow:hidden;background:var(--bg);font-family:"Montserrat",Arial,sans-serif}
  .canvas{position:relative;width:995px;height:1200px}
  .card{position:absolute;left:77px;width:840px;height:560px;background:linear-gradient(135deg,#f7f7f7 0%,#ececec 60%,#e4e4e4 100%);overflow:hidden;box-shadow:0 6px 18px rgba(0,0,0,.25)}
  .card--front{top:30px}
  .card--back{top:610px;background:var(--white)}
  .shapes{position:absolute;inset:0}
  .abs{position:absolute}

  /* front */
  .brand{left:48px;top:52px;color:var(--navy);letter-spacing:6px;line-height:1.15}
  .brand__name{font-size:40px;font-weight:700;display:block}
  .brand__sub{font-size:20px;font-weight:400;letter-spacing:5px;display:block}
  .front-headline{left:48px;top:190px;color:var(--navy);font-weight:800;font-size:26px;line-height:1.25}
  .front-lede{left:48px;top:283px;color:var(--ink);font-weight:300;font-size:20px;line-height:1.25;width:280px}
  .contact-title{left:48px;top:396px;color:var(--navy);font-weight:800;font-size:23px}
  .contact{left:48px;top:434px;color:var(--ink);font-weight:300;font-size:15px;line-height:1.25}
  .contact__phone{display:block;color:var(--navy);font-weight:700;font-size:20px}
  .contact__mail{display:block;font-size:16px}
  .web{color:var(--white);font-size:14px;font-weight:400;letter-spacing:1px}
  .front-web{left:48px;top:522px}

  /* back */
  .services-title{left:40px;top:38px;color:var(--navy);font-weight:800;font-size:26px;line-height:1.2;letter-spacing:.5px}
  .services-lede{left:40px;top:118px;color:var(--ink);font-size:15px;font-weight:400;line-height:1.3}
  .service-grid{left:30px;top:176px;width:400px;display:grid;grid-template-columns:repeat(4,100px);row-gap:12px}
  .service{text-align:center;color:var(--ink);font-size:12.5px;line-height:1.25;height:70px}
  .service svg{display:block;margin:0 auto 4px;width:26px;height:26px;fill:var(--navy)}
  .choice-box{left:438px;top:192px;width:110px;height:106px;background:var(--grey);color:var(--white);font-size:14px;line-height:1.2;text-align:right;padding:20px 12px 0 6px}
  .choose{left:40px;top:352px;color:var(--white);font-weight:800;font-size:16px;line-height:1.28;letter-spacing:.5px}
  .back-contact{left:40px;top:496px;color:var(--white);font-size:12px;line-height:1.2}
  .back-contact b{display:block;font-size:15px;font-weight:700}
  .price{width:113px;background:var(--white);text-align:center;color:var(--ink);font-size:5.8px;line-height:1.5;padding:8px 4px;box-shadow:0 1px 3px rgba(0,0,0,.3)}
  .price__name{color:var(--navy);font-weight:700;font-size:9px}
  .price__tag{font-size:6px;margin-bottom:2px}
  .price__rate{color:var(--navy);font-weight:700;font-size:17px;line-height:1.2}
  .price__unit{margin-bottom:6px}
  .price li{list-style:none;margin-bottom:4px}
  .mail-brand{left:568px;top:32px;color:var(--navy);letter-spacing:2px;line-height:1.2}
  .mail-brand span{display:block;font-size:15px;font-weight:700}
  .mail-brand small{display:block;font-size:6.5px;font-weight:600;letter-spacing:1.5px}
  .return-address{left:568px;top:80px;color:var(--ink);font-size:10px;line-height:1.25}
  .stamp{left:722px;top:30px;width:86px;height:86px;border:1px solid #bcbcbc}
  .address-line{left:568px;width:240px;height:1px;background:#bcbcbc}
  .back-web{left:590px;top:529px}
</style>
</head>
<body>
<main class="canvas">

  <section class="card card--front" aria-label="Postcard front">
    <svg class="shapes" viewBox="0 0 840 560" width="840" height="560">
      <polygon points="590,0 840,0 840,560 330,560" fill="#7b7f86" role="img" aria-label="Photo: person in a striped sweater dropping a house key into an open hand"/>
      <polygon points="505,0 590,0 330,560 250,560" fill="var(--navy)"/>
      <polygon points="400,330 440,330 310,560 265,560" fill="var(--grey-light)" opacity=".9"/>
      <polygon points="0,513 310,513 292,545 0,545" fill="var(--navy)"/>
      <polygon points="0,545 840,545 840,560 0,560" fill="var(--navy-deep)"/>
    </svg>
    <div class="abs brand"><span class="brand__name">BRAMBLECREST</span><span class="brand__sub">PROPERTY MANAGEMENT</span></div>
    <h1 class="abs front-headline">PROPERTY MANAGEMENT<br>ACROSS LUBBOCK, TX</h1>
    <p class="abs front-lede">Maximize your financial returns with support from our rental specialists</p>
    <h2 class="abs contact-title">Contact Our Team</h2>
    <p class="abs contact">Call Now:<span class="contact__phone">(806) 555-0142</span><span class="contact__mail">info@bramblecrestpm.com</span></p>
    <p class="abs web front-web">www.bramblecrestpm.com</p>
  </section>

  <section class="card card--back" aria-label="Postcard back">
    <svg class="shapes" viewBox="0 0 840 560" width="840" height="560">
      <rect x="0" y="0" width="548" height="330" fill="var(--paper)"/>
      <polygon points="335,0 548,0 548,158 377,158" fill="#8e9aae" role="img" aria-label="Photo: two smiling men in suits reviewing a document at a table"/>
      <polygon points="290,0 320,0 385,158 370,158" fill="var(--navy)"/>
      <rect x="0" y="330" width="548" height="230" fill="var(--band)"/>
      <polygon points="548,520 840,520 840,530 548,530" fill="var(--grey-light)"/>
      <rect x="548" y="530" width="292" height="30" fill="var(--navy)"/>
    </svg>

    <h2 class="abs services-title">DISCOVER OUR<br>SERVICES</h2>
    <p class="abs services-lede">We offer full-service property<br>management solutions</p>

    <div class="abs service-grid">
      <div class="service"><svg viewBox="0 0 24 24"><path d="M12 3 2 12h3v8h5v-5h4v5h5v-8h3z"/></svg>Property<br>Marketing</div>
      <div class="service"><svg viewBox="0 0 24 24"><circle cx="8" cy="8" r="3.5"/><circle cx="16" cy="8" r="3.5"/><path d="M1 19c0-4 3-6 7-6s7 2 7 6zM13 19c0-2-.5-3.5-1.5-4.8 1.2-.8 2.8-1.2 4.5-1.2 4 0 7 2 7 6z"/></svg>Tenant<br>Screening</div>
      <div class="service"><svg viewBox="0 0 24 24"><path d="M11 2h2v2.1c2.3.3 4 1.6 4.3 3.7h-2.6c-.3-1-1.3-1.6-2.7-1.6-1.6 0-2.5.7-2.5 1.7 0 1.1 1.1 1.5 3.2 2 2.8.6 4.8 1.5 4.8 4.1 0 2.2-1.8 3.6-4.5 3.9V20h-2v-2.1c-2.6-.3-4.5-1.8-4.7-4h2.6c.2 1.2 1.4 1.9 3.2 1.9 1.7 0 2.7-.7 2.7-1.7s-.8-1.5-3.1-2c-2.9-.6-4.9-1.6-4.9-4 0-2 1.6-3.4 4.1-3.8z"/></svg>Rent<br>Collection</div>
      <div class="service"><svg viewBox="0 0 24 24"><path d="M11 3h2v15h5v2H6v-2h5zM3 7h18v1.6H3zM5 8l-3 6c0 1.7 1.4 2.5 3 2.5S8 15.7 8 14zm0 2.2L6.6 14H3.4zM19 8l-3 6c0 1.7 1.4 2.5 3 2.5s3-.8 3-2.5zm0 2.2 1.6 3.8h-3.2z"/></svg>Legal<br>Guidance</div>
      <div class="service"><svg viewBox="0 0 24 24"><path d="M13 3h6l3 3-2 2-2-1-2 2 1 1-9 10-3-3 10-9 1 1 2-2-1-2z"/></svg>Maintenance</div>
      <div class="service"><svg viewBox="0 0 24 24"><path d="M10 3a7 7 0 0 1 5.6 11.2l5.6 5.6-1.6 1.6-5.6-5.6A7 7 0 1 1 10 3zm0 2.4a4.6 4.6 0 1 0 0 9.2 4.6 4.6 0 0 0 0-9.2z"/></svg>Property<br>Inspections</div>
      <div class="service"><svg viewBox="0 0 24 24"><path d="M3 4h1.6v14.4H21V20H3zM7 12h1.6v5H7zm3-4h1.6v9H10zm3 2h1.6v7H13zm3-4h1.6v11H16z"/></svg>Financial<br>Reporting</div>
      <div class="service"><svg viewBox="0 0 24 24"><path d="M12 2 4 5v6c0 5 3.4 9.4 8 11 4.6-1.6 8-6 8-11V5zm0 2.2V19.8C8.6 18.3 6.2 14.9 6.2 11V6.5z"/></svg>Evictions</div>
    </div>

    <p class="abs choice-box">Make the right choice for your investment.</p>

    <h3 class="abs choose">CHOOSE<br>THE RIGHT<br>PROPERTY<br>MANAGEMENT<br>SYSTEM</h3>
    <p class="abs back-contact">Call Now:<b>(806) 555-0142</b>info@bramblecrestpm.com</p>

    <div class="abs price" style="left:182px;top:342px;height:180px">
      <div class="price__name">Lease Only</div>
      <div class="price__tag">- You Just Need Tenants -</div>
      <div class="price__rate">9%</div>
      <div class="price__unit">of annual lease</div>
      <ul><li>Professional Photography</li><li>Marketing &amp; Advertising</li><li>Property Showings</li><li>Tenant Screening &amp; Qualifications</li><li>Lease Execution</li><li>Move In Coordination</li></ul>
    </div>
    <div class="abs price" style="left:300px;top:336px;height:198px">
      <div class="price__name">Full Service</div>
      <div class="price__tag">- Our Most Popular -</div>
      <div class="price__rate">10%</div>
      <div class="price__unit">of monthly rent</div>
      <ul><li>Includes Leasing Service</li><li>24/7 Emergency Response</li><li>Move In &amp; Out Inspections</li><li>Professional Lease Enforcement</li><li>Schedule &amp; Oversee all Repairs</li><li>Pay all Invoices</li><li>Monthly &amp; Year End Statements</li><li>Annual Market Rent Analysis</li></ul>
    </div>
    <div class="abs price" style="left:418px;top:342px;height:126px">
      <div class="price__name">Premium Service</div>
      <div class="price__tag">- Our Premier Service -</div>
      <div class="price__rate">12%</div>
      <div class="price__unit">of monthly rent</div>
      <ul><li>Includes Full Service Features</li><li>Professional Video Marketing</li><li>Home Warranty Coordination</li><li>Tenant Retention Program</li></ul>
    </div>

    <div class="abs mail-brand"><span>BRAMBLECREST</span><small>PROPERTY MANAGEMENT</small></div>
    <p class="abs return-address">2387 Hollow Pine Road<br>Lubbock, TX 79852</p>
    <div class="abs stamp"></div>
    <div class="abs address-line" style="top:184px"></div>
    <div class="abs address-line" style="top:250px"></div>
    <div class="abs address-line" style="top:316px"></div>
    <p class="abs web back-web">www.bramblecrestpm.com</p>
  </section>

</main>
</body>
</html>
```